BRANDEMEIER & BRANDEMEIER,LLP NEEDS A NEW LETTERHEAD DESIGN

a conservative yet contemporary layout befitting a long established
firm, consistent with the times, some form of logo so it catches ones attention, and is
admirable, but portrays integrity
Updates

I would like to approve #22066987 Please advise how to do this as it’s confusing on the site so I can approve payment for the designer

Target Market(s)

real estate investors and building management people

Industry/Entity Type

Law Firm

Font styles to use
Serif

Colors

Designer to choose colors to be used in the design.

Requirements
Must have
• some form of conservative logo

```html
<!DOCTYPE html>
<html lang="en">
<head>
<meta charset="utf-8">
<title>Brandemeier &amp; Brandemeier, LLP — Letterhead</title>
<link rel="stylesheet" href="https://fonts.googleapis.com/css2?family=Cinzel:wght@400&family=Open+Sans:wght@400;600&display=swap">
<style>
  :root {
    --backdrop: #d8cecb;
    --paper: #fcfcf8;
    --ink: #2e2e2e;
    --ink-soft: #555555;
    --rule: #7a7a7a;
    --band: #383838;
  }
  * { margin: 0; padding: 0; box-sizing: border-box; }
  html, body { width: 1200px; height: 784px; overflow: hidden; }
  body {
    background: var(--backdrop);
    display: flex; align-items: center; justify-content: center;
    font-family: "Open Sans", Arial, sans-serif;
    color: var(--ink);
  }
  .letterhead {
    position: relative;
    width: 540px; height: 764px;
    background: var(--paper);
    box-shadow: 0 2px 10px rgba(0,0,0,.15);
    overflow: hidden;
    padding: 40px 48px 0 60px;
  }
  .masthead { text-align: right; }
  .firm-name {
    font-family: "Cinzel", Georgia, serif;
    font-weight: 400; font-size: 27px; letter-spacing: .5px;
    color: var(--ink);
  }
  .firm-tagline {
    font-family: "Cinzel", Georgia, serif;
    font-size: 8.5px; letter-spacing: .6px;
    color: var(--ink-soft); margin-top: 4px;
  }
  .letter-body { margin-top: 42px; font-size: 10px; line-height: 1.6; color: var(--ink-soft); }
  .salutation { font-size: 11px; color: var(--ink); margin-bottom: 12px; }
  .letter-body p.paragraph { margin-bottom: 14px; }
  .closing { margin-top: 18px; }
  .closing .regards { font-size: 11px; color: var(--ink); margin-bottom: 6px; }
  .closing .signer { font-size: 11px; color: var(--ink); }
  .closing .role { font-size: 9px; color: var(--ink-soft); }
  .footer-rule {
    position: absolute; left: 60px; right: 90px; top: 622px;
    border-top: 1px solid var(--rule);
  }
  .contact {
    position: absolute; left: 60px; top: 634px;
    display: flex; gap: 34px;
    font-size: 8.5px; line-height: 1.8; color: var(--ink-soft); letter-spacing: .3px;
  }
  .contact .icon { display: inline-block; width: 8px; margin-right: 4px; vertical-align: -1px; }
  .corner-band { position: absolute; right: 0; bottom: 0; width: 540px; height: 130px; }
</style>
</head>
<body>
  <main class="letterhead">
    <header class="masthead">
      <h1 class="firm-name">BRANDEMEIER &amp; BRANDEMEIER,LLP</h1>
      <p class="firm-tagline">NEW YORK CITY LANDLORD / TENANT REAL ESTATE LAW</p>
    </header>

    <section class="letter-body">
      <p class="salutation">Dear sir/Madam,</p>
      <p class="paragraph">Lorem ipsum dolor sit amet, an vel recteque dissentiet, detracto albucius platonem ex vel, eros reprimique cu. Atqui aliquando nec an, unum graece adolescens vel ad. Id odio scae has, iudico euismod atomorum ius ea, cum ea honestatis quaerendum theophrastus. Mea honestatis quaerendum theophrastus. Mea</p>
      <p class="paragraph">Lorem ipsum dolor sit amet, an vel recteque dissentiet, detracto albucius platonem ex vel, eros reprimique cu. Atqui aliquando nec an, unum graece adolescens vel ad. Id odio scae has, iudico euismod atomorum ius ea, cum ea honestatis quaerendum theophrastus. Mea dolore reformidans ex, cu cum civibus assentior posidonium. Quo etiam pertinax ex, te eros reprimique cu. Atqui aliquando nec an, unum graece adolescens vel ad. Id odio scae honestatis quaerendum theophrastus. Mea</p>
      <p class="paragraph">Lorem ipsum dolor sit amet, an vel recteque dissentiet, detracto albucius platonem ex vel, eros reprimique cu. Atqui aliquando nec an, unum graece adolescens vel ad. Id odio scae has, iudico euismod atomorum ius ea, cum ea honestatis quaerendum theophrastus. Mea honestatis quaerendum theophrastus. Mea</p>
      <p class="paragraph">eros reprimique cu. Atqui aliquando nec an, unum graece adolescens vel ad. Id odio scae honestatis quaerendum theophrastus. Mea posidonium. Quo etiam pertinax ex, te etiam pertinax ex, te</p>
      <div class="closing">
        <p class="regards">Kind Regards</p>
        <p class="signer">Daniel T. Whitford</p>
        <p class="role">CEO / Founder</p>
      </div>
    </section>

    <div class="footer-rule"></div>
    <footer class="contact">
      <div class="contact-phones">
        <div><svg class="icon" viewBox="0 0 10 10" aria-hidden="true"><path d="M2 1h2l1 2-1.2 1a6 6 0 0 0 2.2 2.2L7 5l2 1v2a1 1 0 0 1-1 1A7 7 0 0 1 1 2a1 1 0 0 1 1-1z" fill="#555"/></svg>+1 555 0142-8670</div>
        <div><svg class="icon" viewBox="0 0 10 10" aria-hidden="true"><rect x="2" y="1" width="6" height="8" rx="1" fill="#555"/></svg>+1 555 0142-8680</div>
      </div>
      <div class="contact-online">
        <div><svg class="icon" viewBox="0 0 10 10" aria-hidden="true"><rect x="1" y="2" width="8" height="6" fill="none" stroke="#555"/><path d="M1 2l4 3 4-3" fill="none" stroke="#555"/></svg>INFO@NORTHGROVE.COM</div>
        <div><svg class="icon" viewBox="0 0 10 10" aria-hidden="true"><circle cx="5" cy="5" r="4" fill="none" stroke="#555"/><path d="M1 5h8M5 1v8" stroke="#555" stroke-width=".7"/></svg>WWW.NORTHGROVE.COM</div>
      </div>
      <div class="contact-address">
        <div>1720 LARKSPUR LANE</div>
        <div>AUSTIN, TX 78701</div>
      </div>
    </footer>

    <svg class="corner-band" viewBox="0 0 540 130" preserveAspectRatio="none" aria-hidden="true">
      <path d="M540 0 C430 70 250 112 0 130 L540 130 Z" fill="var(--band)"/>
      <path d="M540 14 C430 84 250 120 40 130" fill="none" stroke="#ffffff" stroke-width="1.6"/>
    </svg>
  </main>
</body>
</html>
```